Dusty Spur Outfitters Home Page

I need a logo and page design for my home page, maybe some background color suggestions to go with it. I want the logo to project "vintage" and "western wear" but not be your typical trite western saddle and gun type thing.
http://www.dustyspuroutfitters.example/store/cart.php
Not looking for page coding just logo and other design elements to lay in over the site's template to make it "pop"
Reason: Have to finalize the design.
Target Market(s)
My customers are 70/30 men to women.
Industry/Entity Type
Gun

```html
<!DOCTYPE html>
<html lang="en">
<head>
<meta charset="utf-8">
<title>Dusty Spur Outfitters – Home</title>
<link href="https://fonts.googleapis.com/css2?family=Fira+Sans+Condensed:wght@400;500&family=Arimo:wght@400;700&family=Arvo&display=swap" rel="stylesheet">
<style>
:root{
  --header-red:#8a2b30;
  --header-dark:#6f2226;
  --stripe:#2e4851;
  --nav-grey:#cbcac5;
  --page:#f1eee6;
  --brand-red:#9a0d0f;
  --text-dark:#333;
  --text-mid:#555;
  --text-soft:#777;
  --orange:#ee8a5c;
  --footer:#c0441d;
  --green:#8aae4a;
  --star:#e8a317;
  --card:#fff;
  --plate:#efe6cc;
  --plate-ink:#4a3a1e;
}
*{box-sizing:border-box;margin:0;padding:0}
html,body{width:795px;height:1200px;overflow:hidden}
body{background:var(--page);font-family:"Arimo",Arial,sans-serif;color:var(--text-dark);position:relative}
.abs{position:absolute}
.cond{font-family:"Fira Sans Condensed","Arial Narrow",sans-serif}

/* header */
.top-band{left:0;top:0;width:795px;height:68px;background:linear-gradient(var(--header-red),var(--header-dark))}
.top-stripe{left:0;top:68px;width:795px;height:12px;background:var(--stripe)}
.nav{left:0;top:80px;width:795px;height:29px;background:linear-gradient(#d6d5d0,var(--nav-grey))}
.nav a{position:absolute;top:5px;font:400 13px "Fira Sans Condensed",sans-serif;color:#4d4d4d;text-decoration:none}
.cart-icon{left:120px;top:23px;width:27px;height:27px;border-radius:50%;background:#7a2428;box-shadow:inset 0 0 0 1px #9a3a3e}
.cart-text{left:158px;top:21px;color:#f3e6e6;font:400 11.5px "Fira Sans Condensed",sans-serif;line-height:16px}
.cart-text small{font-size:9.5px}
.search{left:548px;top:20px;width:130px;height:28px;background:linear-gradient(#fafafa,#e2e2e2);border:1px solid #bbb}
.logo-plate{left:322px;top:30px;width:154px;height:96px;background:var(--plate);border-radius:12px;display:flex;align-items:center;justify-content:center;text-align:center;box-shadow:0 2px 4px rgba(0,0,0,.25)}
.logo-plate span{font:500 19px/22px "Fira Sans Condensed",sans-serif;color:var(--plate-ink)}

/* hero */
.hero{left:120px;top:146px;width:556px;height:290px;border:2px solid #e4e1d9;background:linear-gradient(100deg,#e9d9c2 0%,#d9c3a8 25%,#f0d36a 45%,#8fc7c9 60%,#e97fa3 75%,#f0b43c 90%)}
.hero-caption{left:425px;top:292px;width:249px;height:82px;background:rgba(90,90,90,.72)}
.hero-caption p{position:absolute;left:15px;color:#fff;font:500 25px "Fira Sans Condensed",sans-serif}
.hero-arrow{position:absolute;left:205px;width:30px;height:29px;border:1px solid #ddd}

/* sidebar */
.panel-head{background:var(--brand-red);color:#fff;font:400 14px "Fira Sans Condensed",sans-serif;padding:6px 13px}
.categories{left:120px;top:456px;width:135px}
.categories ul{list-style:none;background:#f6f5f2}
.categories li{height:22.7px;border-bottom:1px solid #e6e4de;font-size:8px;color:var(--text-mid);padding:7px 0 0 26px;position:relative}
.categories li::before{content:"›";position:absolute;left:13px;top:5px;font-size:9px}
.subscribe{left:120px;top:797px;width:135px;height:143px;background:var(--orange);text-align:center}
.subscribe h3{color:#fff;font:400 14px/17px "Fira Sans Condensed",sans-serif;margin-top:17px}
.subscribe .field{margin:12px auto 0;width:115px;height:26px;background:#fff;border:1px solid #ddd;font-size:6.5px;color:#777;text-align:left;padding:9px 0 0 9px}
.subscribe .btn{margin:12px auto 0;width:74px;height:22px;border-radius:3px;background:#3a3a3a;color:#fff;font:400 11px "Fira Sans Condensed",sans-serif;padding-top:4px}

/* products */
.featured-head{left:275px;top:456px;width:401px;height:26px;background:var(--brand-red);color:#fff;font:400 11px "Fira Sans Condensed",sans-serif;padding:6px 9px}
.featured-head .nav-dot{position:absolute;top:5px;width:15px;height:15px;border-radius:50%;border:1px solid #d88}
.card{width:126px;height:211px;background:var(--card);border:1px solid #ebe8e1}
.card .photo{height:124px;border-bottom:1px solid #eee;margin:0}
.card h4{font:400 8.5px Arimo,sans-serif;margin:14px 0 0 11px;color:#222}
.card .row{display:flex;justify-content:space-between;margin:14px 11px 0;font-size:8.5px}
.card .stars{color:var(--star);font-size:7px;letter-spacing:.5px}
.card .stars i{color:#ccc;font-style:normal}
.card .add{margin:12px auto 0;width:72px;height:20px;background:var(--brand-red);border-radius:2px;color:#fff;font-size:7.5px;display:flex;align-items:center;justify-content:center;gap:5px}

/* info boxes */
.info{width:261px;height:68px;border:2px solid #e2dfd7;display:flex;align-items:center;justify-content:center;gap:10px}
.info h5{font:400 14px Arvo,serif;color:var(--green);border-bottom:1px solid var(--green);line-height:16px}
.info p{font-size:7.5px;color:var(--text-soft);margin-top:3px}

/* footer */
.footer-line{left:0;top:1044px;width:795px;height:1px;background:#e1ddd3}
.fcol h6{font:400 10.5px Arimo,sans-serif;color:#222;margin-bottom:13px}
.fcol li{list-style:none;font-size:6.5px;color:#333;line-height:13.6px}
.pay{display:grid;grid-template-columns:repeat(3,30px);gap:5px 3px}
.pay span{height:19px;border-radius:2px}
.bottom{left:0;top:1150px;width:795px;height:50px;background:var(--footer)}
.bottom p{position:absolute;left:116px;top:19px;color:#fbe3d8;font-size:7.5px}
.social{position:absolute;top:17px;display:flex;gap:4px;left:584px}
.social span{width:13px;height:13px;border-radius:50%}
</style>
</head>
<body>

<header>
  <div class="abs top-band"></div>
  <div class="abs top-stripe"></div>
  <div class="abs cart-icon">
    <svg width="27" height="27" viewBox="0 0 27 27"><path d="M7 9h2l2 7h7l2-5H10" fill="none" stroke="#f1dede" stroke-width="1.3"/><circle cx="12" cy="18.5" r="1" fill="#f1dede"/><circle cx="17" cy="18.5" r="1" fill="#f1dede"/></svg>
  </div>
  <div class="abs cart-text">Shopping Cart<br><small>Item - $0.00</small></div>
  <div class="abs search">
    <svg class="abs" style="left:106px;top:7px" width="12" height="12" viewBox="0 0 12 12"><circle cx="6.5" cy="5" r="3.5" fill="none" stroke="#bbb" stroke-width="1.3"/><path d="M4 7.5 1 11" stroke="#bbb" stroke-width="1.5"/></svg>
  </div>
  <nav class="abs nav">
    <a style="left:119px">Home</a>
    <a style="left:182px">Shipping</a>
    <a style="left:255px">Returns</a>
    <a style="left:498px">About Us</a>
    <a style="left:578px">Sizing</a>
    <a style="left:640px">Contact</a>
  </nav>
  <div class="abs logo-plate"><span>Dusty Spur<br>Outfitters</span></div>
</header>

<section class="abs hero" role="img" aria-label="Three smiling women in sunglasses holding colourful shopping bags on a city street"></section>
<div class="abs hero-caption">
  <p style="top:7px">FALL COLLECTION</p>
  <p style="top:40px">20% discount</p>
  <span class="hero-arrow" style="top:9px"><svg width="30" height="29"><path d="M17 9l-5 5.5 5 5.5" fill="none" stroke="#fff" stroke-width="1.5"/></svg></span>
  <span class="hero-arrow" style="top:43px"><svg width="30" height="29"><path d="M13 9l5 5.5-5 5.5" fill="none" stroke="#fff" stroke-width="1.5"/></svg></span>
</div>

<aside class="abs categories">
  <div class="panel-head">Categories</div>
  <ul>
    <li>Boots</li><li>Men's Western Wear</li><li>Women's Western Wear</li><li>Brand New Arrivals</li>
    <li>CLEARANCE</li><li>T-Shirts</li><li>Vests</li><li>Accessories</li><li>Jackets</li>
    <li>BELTS</li><li>Hand Bags</li><li>Leather</li><li>On Sale!</li>
  </ul>
</aside>

<aside class="abs subscribe">
  <h3>Subscribe to our<br>mailing list</h3>
  <div class="field">Subscribe to our Newsletter!</div>
  <div class="btn">Subscribe</div>
</aside>

<div class="abs featured-head">FEATURED PRODUCTS
  <span class="nav-dot" style="left:355px"></span><span class="nav-dot" style="left:377px"></span>
</div>

<main>
  <article class="abs card" style="left:275px;top:502px">
    <div class="photo" role="img" aria-label="Man in a black embroidered western shirt" style="background:linear-gradient(#f7f7f7,#d8d2c8 40%,#2a2623)"></div>
    <h4>Men's Western Wear</h4>
    <div class="row"><span>$119.50</span><span class="stars">★★★<i>★★</i></span></div>
    <div class="add">Add To Cart <svg width="10" height="9"><path d="M1 3h8l-1.5 5h-5z" fill="#fff"/></svg></div>
  </article>
  <article class="abs card" style="left:414px;top:502px">
    <div class="photo" role="img" aria-label="Tan lace-up leather boots" style="background:radial-gradient(circle at 55% 55%,#9a8466 0%,#b8a78c 35%,#f6f6f6 70%)"></div>
    <h4>Boots</h4>
    <div class="row"><span>$119.50</span><span class="stars">★★★<i>★★</i></span></div>
    <div class="add">Add To Cart <svg width="10" height="9"><path d="M1 3h8l-1.5 5h-5z" fill="#fff"/></svg></div>
  </article>
  <article class="abs card" style="left:551px;top:502px">
    <div class="photo" role="img" aria-label="Woman in a black embroidered western blouse" style="background:linear-gradient(#f7f7f7,#d6c6b8 40%,#2b1e1c)"></div>
    <h4>Women's Western Wear</h4>
    <div class="row"><span>$119.50</span><span class="stars">★★★<i>★★</i></span></div>
    <div class="add">Add To Cart <svg width="10" height="9"><path d="M1 3h8l-1.5 5h-5z" fill="#fff"/></svg></div>
  </article>
  <article class="abs card" style="left:275px;top:729px">
    <div class="photo" role="img" aria-label="Two leather handbags, black and brown" style="background:radial-gradient(ellipse at 50% 65%,#5a4632 0%,#9c8060 35%,#f6f6f6 70%)"></div>
    <h4>Hand Bags</h4>
    <div class="row"><span>$119.50</span><span class="stars">★★★<i>★★</i></span></div>
    <div class="add">Add To Cart <svg width="10" height="9"><path d="M1 3h8l-1.5 5h-5z" fill="#fff"/></svg></div>
  </article>
  <article class="abs card" style="left:414px;top:729px">
    <div class="photo" role="img" aria-label="Black short-sleeved t-shirt" style="background:radial-gradient(ellipse at 50% 50%,#111 0%,#222 35%,#f6f6f6 62%)"></div>
    <h4>Short Sleeves</h4>
    <div class="row"><span>$119.50</span><span class="stars">★★★<i>★★</i></span></div>
    <div class="add">Add To Cart <svg width="10" height="9"><path d="M1 3h8l-1.5 5h-5z" fill="#fff"/></svg></div>
  </article>
  <article class="abs card" style="left:551px;top:729px">
    <div class="photo" role="img" aria-label="Olive canvas jacket" style="background:radial-gradient(ellipse at 50% 50%,#6f6a4c 0%,#948d6c 35%,#f6f6f6 66%)"></div>
    <h4>Jackets</h4>
    <div class="row"><span>$119.50</span><span class="stars">★★★<i>★★</i></span></div>
    <div class="add">Add To Cart <svg width="10" height="9"><path d="M1 3h8l-1.5 5h-5z" fill="#fff"/></svg></div>
  </article>
</main>

<section class="abs info" style="left:120px;top:958px">
  <svg width="42" height="28" viewBox="0 0 42 28"><rect x="12" y="3" width="28" height="17" fill="#999"/><path d="M12 8H5L1 14v7h11z" fill="#aaa"/><circle cx="8" cy="22" r="3.5" fill="#888"/><circle cx="31" cy="22" r="3.5" fill="#888"/></svg>
  <div><h5>FREE SHIPPING</h5><p>On Order Over <b>$30</b> offer today</p></div>
</section>
<section class="abs info" style="left:415px;top:958px">
  <svg width="30" height="32" viewBox="0 0 30 32"><rect x="1" y="3" width="8" height="24" rx="3" fill="#999"/><rect x="11" y="5" width="17" height="22" rx="2" fill="#aaa"/><g fill="#eee"><rect x="14" y="8" width="11" height="4"/><rect x="14" y="15" width="3" height="3"/><rect x="19" y="15" width="3" height="3"/><rect x="14" y="20" width="3" height="3"/><rect x="19" y="20" width="3" height="3"/></g></svg>
  <div><h5>GIVE US CALL</h5><p>1-800-Spurred (1-800-777-8733)</p></div>
</section>

<div class="abs footer-line"></div>
<footer>
  <div class="abs fcol" style="left:121px;top:1062px"><h6>Information</h6>
    <ul><li>Contact us</li><li>Terms and conditions of use</li><li>About us</li><li>Sitemap</li></ul></div>
  <div class="abs fcol" style="left:297px;top:1061px"><h6 style="color:#666">Customer Support</h6>
    <ul style="color:#666"><li>About Us</li><li>Delivery Information</li><li>Privacy Policy</li><li>Term &amp; Condition</li></ul></div>
  <div class="abs fcol" style="left:455px;top:1062px"><h6>My Account</h6>
    <ul><li>My Product</li><li>My Orders</li><li>My Address</li><li>My Personal Info</li></ul></div>
  <div class="abs fcol" style="left:581px;top:1062px"><h6>Make a Payment</h6>
    <div class="pay">
      <span style="background:#f3c9a4"></span><span style="background:#7fb3d8"></span><span style="background:#2a4f9a"></span>
      <span style="background:#e4e4e4"></span><span style="background:#d9552d"></span><span style="background:#3a3a3a"></span>
    </div></div>
  <div class="abs bottom">
    <p>Copyright © 2014 &nbsp;Dusty Spur Outfitters . All rights reserved.</p>
    <div class="social">
      <span style="background:#3b5b9a"></span><span style="background:#3aa3d8"></span><span style="background:#2b77a8"></span>
      <span style="background:#c4302b"></span><span style="background:#f08a24"></span><span style="background:#d14836"></span>
    </div>
  </div>
</footer>

</body>
</html>
```